Website for BrightlineLabs presentation

We need a new website, ideally as a wordpress there, for BrightlineLabs - we focus on machine learning, big data, data science and data analytics. This website should have two main sections - team presentation, introduction and offered services as static pages, and a blog section.

Target Market(s)

Companies which would like to hire the consultants for data science

Industry/Entity Type

Data Service

Font styles to use
Sans Serif

Colors

Designer to choose colors to be used in the design.

Requirements
Must have
• Wordpress template, blog and presentation pages, nice background images, incorporate the existing logo from brief
Nice to have
• match the word and ppt existing templates for brightline labs

```html
<!DOCTYPE html>
<html lang="en">
<head>
<meta charset="utf-8">
<title>BrightlineLabs</title>
<link rel="stylesheet" href="https://fonts.googleapis.com/css2?family=Montserrat:wght@600;700&family=Lato:wght@400;700&display=swap">
<style>
:root{
  --blue:#1786c5;
  --ink:#333;
  --grey:#555;
  --muted:#777;
  --line:#e2e2e2;
  --panel:#f1f1f1;
  --footer:#2f2f2f;
  --white:#fff;
}
*{box-sizing:border-box;margin:0;padding:0}
html,body{width:1200px;height:2679px;overflow:hidden;background:var(--white)}
body{position:relative;font-family:"Lato",Arial,sans-serif;color:var(--grey)}
.abs{position:absolute}
h1,h2,.brand-name,.btn{font-family:"Montserrat",Arial,sans-serif}

.site-header{top:0;left:0;width:1200px;height:115px}
.brand{left:80px;top:22px;display:flex;align-items:center;gap:12px}
.brand-mark{width:26px;height:26px;border-radius:50%;background:var(--blue)}
.brand-name{font-size:24px;font-weight:700;color:var(--blue);line-height:1.05;letter-spacing:.5px}
.social{left:732px;top:38px;display:flex;gap:10px}
.social span{width:40px;height:40px;border:1px solid #c9c9c9;border-radius:50%}
.btn{left:946px;top:36px;width:177px;height:46px;background:var(--blue);color:var(--white);font-size:18px;font-weight:600;display:flex;align-items:center;justify-content:center;letter-spacing:.3px}

.main-nav{top:115px;left:0;width:1200px;height:52px;border-top:1px solid var(--line);border-bottom:1px solid var(--line)}
.main-nav ul{list-style:none;display:flex;gap:38px;padding-left:78px;height:100%;align-items:center}
.main-nav li{font-size:15px;color:var(--grey);letter-spacing:.5px;position:relative;height:100%;display:flex;align-items:center}
.main-nav li.active::before{content:"";position:absolute;top:-1px;left:0;right:0;height:3px;background:var(--blue)}

.hero{top:167px;left:0;width:1200px;height:633px;background:linear-gradient(180deg,#d8dde3 0%,#e6e9ed 45%,#f3f4f6 80%,#fff 100%)}
.hero-title{top:380px;left:0;width:1200px;text-align:center;font-size:46px;font-weight:700;color:var(--blue)}
.hero-text{top:450px;left:255px;width:690px;text-align:center;font-size:17px;line-height:1.6;color:var(--ink)}

.section-title{left:0;width:1200px;text-align:center;font-size:40px;font-weight:700;color:var(--blue)}
.about-text{top:920px;left:212px;width:776px;text-align:center;font-size:14.5px;line-height:1.75;color:var(--grey)}
.about-text p+p{margin-top:8px}

.services{top:1146px;left:0;width:1200px;height:531px;background:var(--panel)}
.service{width:260px}
.service h3{font-size:22px;font-weight:400;color:#444;margin-bottom:10px}
.service p{font-size:14.5px;line-height:1.7;color:var(--muted)}
.service.left{text-align:right}
.hub{left:507px;top:1340px;width:185px;height:160px;background:var(--white);box-shadow:0 2px 10px rgba(0,0,0,.08);display:flex;align-items:center;justify-content:center}
.hub span{width:56px;height:56px;border-radius:50%;border:3px solid var(--blue)}
.tile-back{width:72px;height:72px;background:#fafafa;box-shadow:0 1px 6px rgba(0,0,0,.06)}
.tile{width:93px;height:93px;background:var(--white);box-shadow:0 2px 10px rgba(0,0,0,.1);display:flex;align-items:center;justify-content:center}

.post{width:322px;height:428px;border:1px solid var(--line);background:var(--white)}
.post-image{height:218px}
.post-date{position:absolute;left:17px;top:151px;width:82px;height:80px;background:var(--blue);color:var(--white);text-align:center;padding-top:12px}
.post-date b{display:block;font-size:29px;font-weight:400;line-height:1}
.post-date small{font-size:16px;letter-spacing:.5px}
.post-body{padding:22px 16px}
.post-body h3{font-size:17.5px;font-weight:700;color:var(--ink);line-height:1.7;margin-bottom:6px}
.post-body p{font-size:14.5px;line-height:1.75;color:var(--muted)}

.contact{top:2315px;left:0;width:1200px;height:312px;background:var(--blue)}
.contact .section-title{color:var(--white);top:55px}
.contact-item{width:300px;text-align:center;color:var(--white);font-size:14.5px;line-height:1.75}
.contact-icon{width:60px;height:60px;border:2px solid var(--white);border-radius:50%;margin:0 auto 16px;display:flex;align-items:center;justify-content:center}

.site-footer{top:2627px;left:0;width:1200px;height:52px;background:var(--footer);color:var(--white);font-size:15px;display:flex;align-items:center;justify-content:center;letter-spacing:.3px}
</style>
</head>
<body>

<header class="site-header abs">
  <div class="brand abs"><span class="brand-mark"></span><span class="brand-name">BRIGHTLINE<br>LABS</span></div>
  <div class="social abs" aria-label="Social profiles"><span></span><span></span><span></span><span></span></div>
  <a class="btn abs">CONTACT NOW</a>
</header>

<nav class="main-nav abs">
  <ul><li class="active">HOME</li><li>ABOUT</li><li>SERVICES</li><li>BLOG</li><li>CONTACT</li></ul>
</nav>

<section class="hero abs" role="img" aria-label="Background photo of a consulting team smiling around a meeting table"></section>
<h1 class="hero-title abs">BRIGHTLINE LABS</h1>
<p class="hero-text abs">Lorem Ipsum is simply dummy text of the printing and typesetting industry. Lorem Ipsum has been the industry's standard dummy text ever since.</p>

<h2 class="section-title abs" style="top:855px">ABOUT BRIGHTLINE LABS</h2>
<div class="about-text abs">
  <p>Lorem Ipsum is simply dummy text of the printing and typesetting industry. Lorem Ipsum has been the industry's standard dummy text ever since the 1500s, when an unknown printer took a galley of type and scrambled it to make a type specimen book. It has survived not only five centuries.</p>
  <p>electronic typesetting, remaining essentially unchanged. It was popularised in the 1960s with the release of Typeline sheets containing Lorem Ipsum passages, and more recently with desktop publishing software like Pagecraft Studio including versions of Lorem Ipsum.</p>
</div>

<section class="services abs"></section>
<h2 class="section-title abs" style="top:1195px">OUR SERVICES</h2>

<div class="service left abs" style="left:96px;top:1285px"><h3>Machine learning</h3><p>Lorem Ipsum is simply dummy text of the printing and typesetting industry.</p></div>
<div class="service abs" style="left:847px;top:1285px"><h3>Data science</h3><p>Lorem Ipsum is simply dummy text of the printing and typesetting industry.</p></div>
<div class="service left abs" style="left:96px;top:1492px"><h3>Big data</h3><p>Lorem Ipsum is simply dummy text of the printing and typesetting industry.</p></div>
<div class="service abs" style="left:847px;top:1492px"><h3>Data analytics</h3><p>Lorem Ipsum is simply dummy text of the printing and typesetting industry.</p></div>

<div class="tile-back abs" style="left:398px;top:1328px"></div>
<div class="tile-back abs" style="left:728px;top:1328px"></div>
<div class="tile-back abs" style="left:398px;top:1536px"></div>
<div class="tile-back abs" style="left:728px;top:1536px"></div>
<div class="hub abs"><span></span></div>

<div class="tile abs" style="left:420px;top:1282px">
  <svg width="50" height="40" viewBox="0 0 50 40" fill="none" stroke="#1786c5" stroke-width="3"><circle cx="17" cy="17" r="8"/><circle cx="17" cy="17" r="3"/><circle cx="36" cy="28" r="6"/><path d="M17 4v5M17 25v5M4 17h5M25 17h5M36 18v3M36 35v3M26 28h3M43 28h3"/></svg>
</div>
<div class="tile abs" style="left:687px;top:1282px">
  <svg width="44" height="44" viewBox="0 0 44 44" fill="none" stroke="#1786c5" stroke-width="2.5"><circle cx="22" cy="22" r="3" fill="#1786c5"/><ellipse cx="22" cy="22" rx="17" ry="7"/><ellipse cx="22" cy="22" rx="17" ry="7" transform="rotate(60 22 22)"/><ellipse cx="22" cy="22" rx="17" ry="7" transform="rotate(120 22 22)"/></svg>
</div>
<div class="tile abs" style="left:420px;top:1490px">
  <svg width="44" height="44" viewBox="0 0 44 44"><g fill="#1786c5"><rect x="4" y="28" width="7" height="12"/><rect x="14" y="22" width="7" height="18"/><rect x="24" y="18" width="7" height="22"/><rect x="34" y="10" width="7" height="30"/></g><polyline points="6,20 16,13 27,16 38,4" fill="none" stroke="#1786c5" stroke-width="2.5"/></svg>
</div>
<div class="tile abs" style="left:687px;top:1490px">
  <svg width="46" height="46" viewBox="0 0 46 46" fill="none" stroke="#1786c5" stroke-width="3"><circle cx="19" cy="19" r="12"/><path d="M28 28l13 13"/><polyline points="12,23 17,17 21,20 27,12" stroke-width="2"/></svg>
</div>

<h2 class="section-title abs" style="top:1727px">LATEST BLOG</h2>

<article class="post abs" style="left:78px;top:1797px">
  <div class="post-image" role="img" aria-label="Photo of colleagues talking around an office table" style="background:linear-gradient(135deg,#8a8178,#c9bfb4 50%,#6f6a66)"></div>
  <div class="post-date"><b>17</b><small>MAY</small></div>
  <div class="post-body"><h3>Lorem Ipsum is simply dummy text of the printing.</h3><p>Lorem Ipsum is simply dummy text of the printing and typesetting industry. Lorem Ipsum has been the industry's standard.</p></div>
</article>
<article class="post abs" style="left:439px;top:1797px">
  <div class="post-image" role="img" aria-label="Photo of hands working at a laptop with charts on the desk" style="background:linear-gradient(135deg,#9fb3c4,#dfe7ee 55%,#aebdca)"></div>
  <div class="post-date"><b>17</b><small>MAY</small></div>
  <div class="post-body"><h3>Lorem Ipsum is simply dummy text of the printing.</h3><p>Lorem Ipsum is simply dummy text of the printing and typesetting industry. Lorem Ipsum has been the industry's standard.</p></div>
</article>
<article class="post abs" style="left:800px;top:1797px">
  <div class="post-image" role="img" aria-label="Photo of a hand using a calculator beside a laptop" style="background:linear-gradient(135deg,#b9b6b2,#e4e2df 55%,#8d8a87)"></div>
  <div class="post-date"><b>17</b><small>MAY</small></div>
  <div class="post-body"><h3>Lorem Ipsum is simply dummy text of the printing.</h3><p>Lorem Ipsum is simply dummy text of the printing and typesetting industry. Lorem Ipsum has been the industry's standard.</p></div>
</article>

<section class="contact abs">
  <h2 class="section-title abs">CONTACT US</h2>
  <svg class="abs" style="left:390px;top:150px" width="400" height="30" viewBox="0 0 400 30" fill="none" stroke="#fff" stroke-width="1.5">
    <circle cx="6" cy="8" r="4"/><path d="M10 8h150M10 14h130M240 14h140M262 20h110"/><circle cx="386" cy="20" r="4"/>
  </svg>
  <div class="contact-item abs" style="left:135px;top:133px">
    <div class="contact-icon"><svg width="22" height="22" viewBox="0 0 24 24" fill="#fff"><path d="M6.6 10.8a15 15 0 006.6 6.6l2.2-2.2c.3-.3.7-.4 1-.2 1.1.4 2.3.6 3.6.6.6 0 1 .4 1 1V20c0 .6-.4 1-1 1A17 17 0 013 4c0-.6.4-1 1-1h3.5c.6 0 1 .4 1 1 0 1.3.2 2.5.6 3.6.1.3 0 .7-.2 1z"/></svg></div>
    123 456 7890
  </div>
  <div class="contact-item abs" style="left:437px;top:133px">
    <div class="contact-icon"><svg width="20" height="24" viewBox="0 0 20 24" fill="none" stroke="#fff" stroke-width="2"><path d="M10 23s8-8 8-13a8 8 0 00-16 0c0 5 8 13 8 13z"/><circle cx="10" cy="10" r="3"/></svg></div>
    Lorem Ipsum is simply dummy text of<br>the printing and typesetting.
  </div>
  <div class="contact-item abs" style="left:738px;top:133px">
    <div class="contact-icon"><svg width="22" height="16" viewBox="0 0 22 16" fill="none" stroke="#fff" stroke-width="2"><rect x="1" y="1" width="20" height="14" rx="2"/><path d="M1 2l10 7 10-7"/></svg></div>
    info@brightlinelabs.com
  </div>
</section>

<footer class="site-footer abs">©BRIGHTLINE LABS- 2018. All Rights Reserved.</footer>

</body>
</html>
```